Landing Page for Church Launch

We are a new Christian Church Plant in Milwaukee Wisconsin. I would like an exciting and unique landing page for people who are interested in:
1) What our ministry is about
2) When our ministry will be launching
3) Those who may want to join our launch team
4) Those who may want give financially into our vision
5) Those who want to follow us and get more information about us
I would also love for our color scheme to be reflective of our logo.
I included more detailed instructions and what we are looking for in the enclosed document
Religious/Christian

```html
<!DOCTYPE html>
<html lang="en">
<head>
<meta charset="utf-8">
<title>Renew Church – Launching Soon</title>
<link href="https://fonts.googleapis.com/css2?family=Prompt:wght@400;500;600&family=Roboto:wght@400;500;700&display=swap" rel="stylesheet">
<style>
:root{
  --red:#c3000f;
  --red-dark:#a5000c;
  --navy:#1b0f7a;
  --navy-dark:#140a5e;
  --ink:#111;
  --text:#555;
  --white:#fff;
  --footer:#0b0b0d;
  --head:'Prompt',sans-serif;
  --body:'Roboto',sans-serif;
}
*{box-sizing:border-box;margin:0;padding:0}
html,body{width:1200px;height:4655px;overflow:hidden}
body{position:relative;background:var(--white);font-family:var(--body);color:var(--text)}
.abs{position:absolute}
/* hero */
.hero{left:0;top:0;width:1200px;height:705px;overflow:hidden}
.hero-photo{position:absolute;inset:0;background:radial-gradient(ellipse at 60% 30%,#a07a5e 0%,#6b4e3e 35%,#3a302c 70%,#26211f 100%)}
.hero-shade{position:absolute;inset:0;background:linear-gradient(180deg,rgba(0,0,0,.15),rgba(0,0,0,.45))}
.brand{left:112px;top:22px;font-family:var(--head);font-weight:600;font-size:30px;color:var(--white);display:flex;align-items:center;gap:10px;letter-spacing:1px}
.brand i{width:14px;height:14px;background:var(--red);display:block}
.menu{left:1048px;top:32px;width:40px}
.menu span{display:block;height:3px;background:var(--white);margin-bottom:8px;border-radius:2px}
.hero-kicker{left:0;width:1200px;text-align:center;font-family:var(--head);color:var(--white);font-size:20px;letter-spacing:.5px}
.hero-date{left:0;top:350px;width:1200px;text-align:center;font-family:var(--head);font-weight:600;font-size:40px;color:var(--white)}
.count{top:488px;width:65px;height:47px;background:var(--red);color:var(--white);font-family:var(--head);font-weight:500;font-size:21px;display:flex;align-items:center;justify-content:center;border-radius:3px}
.count-lbl{top:543px;width:65px;text-align:center;color:var(--white);font-size:15px}
/* shared */
.sec-title{font-family:var(--head);font-weight:500;font-size:31px;color:var(--ink);letter-spacing:.5px}
.para{font-size:14px;line-height:25.5px;color:var(--text)}
.btn{display:flex;align-items:center;justify-content:center;gap:8px;font-family:var(--body);font-weight:700;font-size:12.5px;color:var(--white);text-transform:uppercase;border-radius:3px}
.btn.red{background:var(--red)}
.btn.navy{background:var(--navy)}
.btn.white{background:var(--white);color:var(--navy)}
.btn.white.on-red{color:var(--red)}
.arrow{width:12px;height:12px;border-radius:50%;background:currentColor;position:relative;display:inline-block}
.arrow::after{content:"";position:absolute;left:3px;top:3px;border-left:6px solid var(--white);border-top:3px solid transparent;border-bottom:3px solid transparent}
.btn.white .arrow::after{border-left-color:var(--white)}
.ticks li{list-style:none;position:relative;padding-left:28px;font-size:14px;color:var(--text);line-height:25.5px}
.ticks li::before{content:"";position:absolute;left:0;top:7px;width:12px;height:12px;border-radius:50%;background:var(--red)}
.ticks li::after{content:"";position:absolute;left:3px;top:10px;width:5px;height:3px;border-left:2px solid #fff;border-bottom:2px solid #fff;transform:rotate(-45deg)}
.photo{background:linear-gradient(160deg,#c9d0cf,#8f9893 50%,#5f6a66)}
.sub{font-weight:700;font-size:14px;color:var(--ink)}
/* vision/mission */
.vm-title{font-family:var(--head);font-weight:500;font-size:21px;color:var(--white)}
.vm-text{font-size:13.5px;line-height:25px;color:var(--white)}
.vm-icon{width:80px;height:80px;border-radius:50%;background:var(--white);display:flex;align-items:center;justify-content:center}
/* links */
.link{font-weight:500;font-size:16px;color:var(--red);text-decoration:underline;display:flex;align-items:center;gap:12px}
.link i{width:14px;height:14px;border-radius:50%;border:2px solid var(--navy);position:relative}
.link i::after{content:"";position:absolute;left:3px;top:3px;width:4px;height:4px;border-radius:50%;background:var(--navy)}
.give-text{left:100px;top:2950px;width:1000px;text-align:center;font-family:var(--head);font-size:32px;line-height:54px;color:var(--white)}
/* contact */
.field{left:112px;width:423px;background:var(--white);border:1px solid #ddd;font-size:11px;color:#666;padding:13px 16px}
.c-head{font-family:var(--head);font-weight:500;font-size:28px;color:var(--white)}
.c-lbl{font-weight:700;font-size:14px;color:var(--white)}
.c-txt{font-size:14px;line-height:23px;color:var(--white)}
.social{width:32px;height:32px;border-radius:50%;background:var(--white);border:2px solid var(--red)}
.footer-social{width:40px;height:40px;border-radius:50%;background:var(--white)}
.footer-social.red{background:var(--red)}
</style>
</head>
<body>

<!-- Hero -->
<section class="abs hero">
  <div class="hero-photo" role="img" aria-label="Smiling woman talking with friends in a warm indoor setting"></div>
  <div class="hero-shade"></div>
  <svg class="abs" style="left:0;top:0" width="1200" height="705" viewBox="0 0 1200 705">
    <polygon points="0,705 0,700 600,658 1200,700 1200,705" fill="#fff"/>
    <polygon points="700,705 1200,648 1200,705" fill="#c3000f"/>
    <polygon points="0,705 600,658 1200,705" fill="#fff"/>
  </svg>
</section>
<div class="abs brand"><i></i>RENEW</div>
<div class="abs menu"><span></span><span></span><span></span></div>
<div class="abs hero-kicker" style="top:307px">WE ARE COMING</div>
<div class="abs hero-date">SEPTEMBER 16, 2023AT 5PM</div>
<div class="abs hero-kicker" style="top:428px">RENEW IS COMING</div>
<div class="abs count" style="left:445px">230</div>
<div class="abs count" style="left:524px">08</div>
<div class="abs count" style="left:605px">15</div>
<div class="abs count" style="left:685px">35</div>
<div class="abs count-lbl" style="left:445px">Days</div>
<div class="abs count-lbl" style="left:524px">Hour</div>
<div class="abs count-lbl" style="left:605px">Min</div>
<div class="abs count-lbl" style="left:685px">Sec</div>

<!-- Launch team -->
<h2 class="abs sec-title" style="left:0;top:755px;width:1200px;text-align:center">LAUNCH TEAM</h2>
<p class="abs para" style="left:262px;top:810px;width:678px;text-align:center">Renew is tentatively scheduled to reopen physical doors on September 16, 2023. In preparation for those we are called to serve, we will have a launch team to help lay the groundwork to make a lasting impact and change in our community. Some of the asks of the launch team will be:</p>
<div class="abs" style="left:104px;top:1575px;width:476px;height:28px;background:#dcdce6"></div>
<div class="abs photo" style="left:108px;top:922px;width:480px;height:663px;border:6px solid #fff;box-shadow:0 0 14px rgba(0,0,0,.12)" role="img" aria-label="Portrait of the lead pastor in a plaid blazer"></div>
<ul class="abs ticks" style="left:636px;top:930px;width:470px;line-height:34px">
  <li style="line-height:34px">Pray for the church</li>
  <li style="line-height:34px">Attend monthly launch team meetings (For Planning and Strategy)</li>
  <li style="line-height:34px">Invite others to the launch team and events we host</li>
  <li style="line-height:34px">Volunteer at community and networking outreach events</li>
</ul>
<p class="abs para" style="left:636px;top:1076px;width:455px">Launch team members have no obligation to stay with the ministry once it’s launched. Launch Team members are willing to use their time and talents to help establish another Kingdom Destination here in the earth. We’d love for you to stay around, but we rather you follow the purpose God has put in your heart.</p>
<div class="abs btn red" style="left:636px;top:1218px;width:199px;height:44px">Join our launch team</div>
<div class="abs sub" style="left:636px;top:1292px">Prayer Group</div>
<p class="abs para" style="left:636px;top:1323px;width:455px">Pray for us as directed through email and video from Pastor Sam<br>Join our Prayer Team</p>
<div class="abs btn navy" style="left:636px;top:1390px;width:199px;height:43px">Join our prayer team</div>
<div class="abs sub" style="left:636px;top:1464px">Give</div>
<p class="abs para" style="left:636px;top:1495px;width:455px">Pray for us as directed through email and video from Pastor Sam<br>Join our Prayer Team</p>
<div class="abs btn red" style="left:636px;top:1559px;width:193px;height:46px">Give Online</div>

<!-- Vision / Mission -->
<svg class="abs" style="left:0;top:1670px" width="1200" height="450" viewBox="0 0 1200 450">
  <defs>
    <linearGradient id="navyBand" x1="0" y1="0" x2="0" y2="1"><stop offset="0" stop-color="#1b0f7a"/><stop offset="1" stop-color="#231280"/></linearGradient>
    <linearGradient id="redBand" x1="0" y1="0" x2="0" y2="1"><stop offset="0" stop-color="#c3000f"/><stop offset="1" stop-color="#a5000c"/></linearGradient>
  </defs>
  <polygon points="0,5 600,40 600,444 0,444" fill="url(#navyBand)"/>
  <polygon points="600,40 1200,0 1200,444 600,444" fill="url(#redBand)"/>
  <polygon points="0,444 0,400 600,440 1200,400 1200,444" fill="#fff"/>
</svg>
<div class="abs vm-icon" style="left:112px;top:1758px">
  <svg width="46" height="46" viewBox="0 0 46 46" fill="none" stroke="#1b0f7a" stroke-width="2.5"><path d="M3 23c6-9 13-13 20-13s14 4 20 13c-6 9-13 13-20 13S9 32 3 23z"/><circle cx="23" cy="23" r="6"/><path d="M2 10V2h8M36 2h8v8M44 36v8h-8M10 44H2v-8"/></svg>
</div>
<div class="abs vm-title" style="left:219px;top:1783px">Vision</div>
<p class="abs vm-text" style="left:112px;top:1868px;width:400px">A Faith Community established to connect YOU to Jesus, YOUR Purpose, and the Community YOU serve.</p>
<div class="abs btn white" style="left:112px;top:1975px;width:163px;height:43px">Learn more <span class="arrow"></span></div>
<div class="abs vm-icon" style="left:677px;top:1758px">
  <svg width="46" height="46" viewBox="0 0 46 46" fill="none" stroke="#c3000f" stroke-width="2.5"><circle cx="21" cy="25" r="17"/><circle cx="21" cy="25" r="10"/><circle cx="21" cy="25" r="3"/><path d="M21 25L40 6M34 6h6v6"/></svg>
</div>
<div class="abs vm-title" style="left:784px;top:1783px">Mission</div>
<p class="abs vm-text" style="left:678px;top:1860px;width:410px">To be the spiritual destination of choice for those seeking to connect to Jesus in a Christ-Centered, Multi-Ethnic community that serves families with and without special needs.</p>
<div class="abs btn white on-red" style="left:683px;top:1975px;width:163px;height:43px">Learn more <span class="arrow"></span></div>

<!-- Why open -->
<h2 class="abs sec-title" style="left:0;top:2181px;width:1200px;text-align:center;padding-left:40px">WHY OPEN ANOTHER CHURCH?</h2>
<ul class="abs ticks" style="left:112px;top:2263px;width:485px;text-align:justify">
  <li style="margin-bottom:10px">76% of people in the Milwaukee Metropolitan Area are not part of a faith community. There has to be an organization that addresses the needs of the people in this community.</li>
  <li style="margin-bottom:10px">Milwaukee is known as one of the most segregated big cities in the United States. What better way to begin to break ground towards unity than by creating a worship space that reflects heaven?</li>
  <li style="margin-bottom:10px">Research shows only 10 percent of people who have a child with special needs are part of a faith community. We must address the physical and mental needs of families who have children with disabilities, showering them with the love of God and the support of a like-minded community</li>
  <li>Have you ever asked Why am I Here? What is my Purpose? If so, you are not alone. We help people find their purpose and connect them back to the community they serve.</li>
</ul>
<div class="abs link" style="left:112px;top:2684px"><i></i>Core Values</div>
<div class="abs link" style="left:268px;top:2684px"><i></i>Pastor Sam</div>
<div class="abs" style="left:690px;top:2270px;width:398px;height:390px;background:#f8dede"></div>
<div class="abs" style="left:672px;top:2286px;width:398px;height:401px;background:linear-gradient(180deg,#7d84c8 0%,#c79ab6 45%,#8a5572 75%,#2d2143 100%)" role="img" aria-label="Worshippers raising hands before a cross at sunset, video thumbnail"></div>
<div class="abs" style="left:660px;top:2318px;width:383px;height:387px;border:2px solid var(--red)"></div>
<svg class="abs" style="left:850px;top:2464px" width="46" height="46" viewBox="0 0 46 46"><circle cx="23" cy="23" r="23" fill="#fff"/><circle cx="23" cy="23" r="16" fill="#111"/><polygon points="19,15 31,23 19,31" fill="#fff"/></svg>

<!-- Giving band -->
<svg class="abs" style="left:0;top:2775px" width="1200" height="560" viewBox="0 0 1200 560">
  <polygon points="0,0 600,40 0,50" fill="#c3000f"/>
  <polygon points="0,48 600,40 1200,10 1200,550 600,505 0,550" fill="#1b0f7a"/>
  <polygon points="0,550 600,505 1200,550 1200,560 0,560" fill="#fff"/>
</svg>
<p class="abs give-text">Join this movement through your giving. Contribute to advancing the Kingdom of Heaven on Earth. If the Lord has placed it on your heart to give into this visio</p>
<div class="abs btn red" style="left:524px;top:3159px;width:154px;height:43px">Click here <span class="arrow" style="color:#fff"></span><style>.give-arrow{}</style></div>

<!-- Community -->
<div class="abs" style="left:112px;top:3555px;width:24px;height:24px;border-radius:50%;background:var(--red)"></div>
<div class="abs" style="left:112px;top:3589px;width:24px;height:24px;border-radius:50%;background:var(--navy)"></div>
<div class="abs" style="left:167px;top:3402px;width:348px;height:348px;border-radius:50%;border:3px solid var(--navy);background:radial-gradient(circle at 40% 45%,#e8c47a,#b48e60 45%,#6b5a48)" role="img" aria-label="Volunteers sharing a meal and a prayer together"></div>
<div class="abs" style="left:397px;top:3635px;width:138px;height:138px;border-radius:50%;border:3px solid #fff;background:radial-gradient(circle,#8a6a55,#3e2f28)" role="img" aria-label="Hands joined together in prayer"></div>
<h2 class="abs sec-title" style="left:623px;top:3480px;width:480px;text-align:right;font-size:30px">COMMUNITY INVOLVEMENT</h2>
<p class="abs para" style="left:643px;top:3555px;width:443px;text-align:justify">We are looking to partner with organizations that are making a difference in our community. If you are an organization which serves families with special needs, are focused on helping people develop in purpose, or helping to meet some of the basic needs of our community, we would love to explore collaboration and partnership to serve families.</p>

<!-- Contact -->
<svg class="abs" style="left:0;top:3820px" width="1200" height="530" viewBox="0 0 1200 530">
  <polygon points="0,0 600,40 600,530 0,530" fill="#c3000f"/>
  <polygon points="600,40 1200,0 1200,530 600,530" fill="#1b0f7a"/>
  <polygon points="0,0 600,20 1200,0" fill="#1b0f7a"/>
</svg>
<h3 class="abs c-head" style="left:112px;top:3928px">Get In Touch</h3>
<div class="abs field" style="top:3999px;height:43px">&#9675;&nbsp; Name,</div>
<div class="abs field" style="top:4058px;height:42px">&#9742;&nbsp; Phone Number</div>
<div class="abs field" style="top:4113px;height:84px">&#9993;&nbsp; Email</div>
<div class="abs btn navy" style="left:112px;top:4230px;width:145px;height:40px;font-size:13px">Submit now</div>
<h3 class="abs c-head" style="left:707px;top:3928px">Contact Details</h3>
<svg class="abs" style="left:706px;top:4000px" width="28" height="36" viewBox="0 0 28 36"><path d="M14 0C6 0 0 6 0 14c0 10 14 22 14 22s14-12 14-22C28 6 22 0 14 0z" fill="#fff"/><circle cx="14" cy="14" r="5" fill="#1b0f7a"/></svg>
<p class="abs c-txt" style="left:766px;top:3993px;width:300px">123, Lorem ipsum dolor consectetur adipiscing elited sed doied.</p>
<svg class="abs" style="left:702px;top:4072px" width="36" height="36" viewBox="0 0 36 36" fill="none" stroke="#fff" stroke-width="2"><path d="M8 4l6 7-4 4c2 5 6 9 11 11l4-4 7 6-4 5C15 32 4 21 3 8z"/><path d="M20 6a10 10 0 0 1 10 10M20 1a15 15 0 0 1 15 15"/></svg>
<div class="abs c-lbl" style="left:766px;top:4071px">PHONE NUMBER</div>
<div class="abs c-txt" style="left:766px;top:4094px">555-014-2290</div>
<svg class="abs" style="left:702px;top:4152px" width="38" height="28" viewBox="0 0 38 28" fill="none" stroke="#fff" stroke-width="2"><rect x="1" y="1" width="36" height="26"/><path d="M1 1l18 15L37 1M1 27l13-13M37 27L24 14"/></svg>
<div class="abs c-lbl" style="left:766px;top:4142px">EMAIL</div>
<div class="abs c-txt" style="left:766px;top:4165px">hello@renewchurch.org</div>
<div class="abs social" style="left:707px;top:4223px" role="img" aria-label="Social profile link"></div>
<div class="abs social" style="left:750px;top:4223px" role="img" aria-label="Video channel link"></div>
<div class="abs social" style="left:792px;top:4223px" role="img" aria-label="Photo profile link"></div>

<!-- Footer -->
<footer class="abs" style="left:0;top:4346px;width:1200px;height:309px;background:var(--footer)">
  <div class="abs" style="left:0;top:60px;width:1200px;display:flex;justify-content:center;align-items:center;gap:10px;font-family:var(--head);font-weight:600;font-size:32px;color:#fff;letter-spacing:1px"><i style="width:14px;height:14px;background:var(--red);display:block"></i>RENEW</div>
  <p class="abs" style="left:0;top:154px;width:1200px;text-align:center;font-size:13px;color:#fff">Copyright© 2023 <u>Renew Church</u> &nbsp;|&nbsp; All Rights Reserved</p>
  <div class="abs footer-social red" style="left:551px;top:218px" role="img" aria-label="Social profile link"></div>
  <div class="abs footer-social" style="left:603px;top:218px" role="img" aria-label="Video channel link"></div>
  <div class="abs footer-social" style="left:656px;top:218px" role="img" aria-label="Photo profile link"></div>
</footer>

</body>
</html>
```